Landingpage Design X-Mas Invitation

Every year we invite customers to a special X-Mas Apéro. Since we are an IT-Company we handle the registration process by a landingpage. For this we need a design for the event 2016. The content will be the same as 2015 (you will finde the design attached from last year. There will be an additional job for creating the E-Mail.

Target Market(s)

Customers of IT Company, medium Companys in Central Switzerland

Industry/Entity Type

It Company

Number of Pages Required

1 page

Requirements
Must have
• Christmas Style

```html
<!DOCTYPE html>
<html lang="de">
<head>
<meta charset="utf-8">
<title>Lumenar IT Solutions – Weihnachtsapéro 2016</title>
<link href="https://fonts.googleapis.com/css2?family=Bree+Serif&family=Dosis:wght@400;500;600&family=Lobster&display=swap" rel="stylesheet">
<style>
  :root {
    --brand-red: #c8432c;
    --ink: #2f3437;
    --field-border: #d9534a;
    --snow-top: #e6ecee;
    --snow-mid: #f1f5f6;
    --pine: #1f5e35;
    --white: #ffffff;
    --partner-ink: #3a3f44;
    --decor-red: #c63a2c;
    --decor-gold: #b89436;
    --decor-green: #2c5a22;
  }
  * { box-sizing: border-box; margin: 0; padding: 0; }
  html, body { width: 1200px; height: 974px; overflow: hidden; }
  body {
    position: relative;
    background: radial-gradient(ellipse at 50% 35%, var(--snow-mid) 0%, var(--snow-top) 60%, #dfe6e8 100%);
    font-family: "Bree Serif", serif;
    color: var(--ink);
  }
  .corner-decor {
    position: absolute; top: 0; width: 215px; height: 230px;
  }
  .corner-decor--left {
    left: 0;
    background: radial-gradient(ellipse 100% 100% at 0 0,
      var(--decor-red) 0%, var(--decor-gold) 30%, var(--decor-green) 55%,
      rgba(44,90,34,0.4) 78%, rgba(44,90,34,0) 100%);
  }
  .corner-decor--right {
    right: 0;
    background: radial-gradient(ellipse 100% 100% at 100% 0,
      var(--decor-red) 0%, var(--decor-gold) 30%, var(--decor-green) 55%,
      rgba(44,90,34,0.4) 78%, rgba(44,90,34,0) 100%);
  }
  .brand { position: absolute; top: 48px; left: 448px; width: 304px; text-align: center; }
  .brand__name { font-family: "Bree Serif", serif; font-size: 74px; line-height: 1; color: var(--brand-red); }
  .brand__tag {
    display: block; margin-top: 8px; text-align: right;
    font-family: "Dosis", sans-serif; font-size: 19px; letter-spacing: 1.5px; color: var(--ink);
  }
  .intro {
    position: absolute; top: 203px; left: 80px; width: 1040px;
    text-align: center; font-size: 19.5px; line-height: 31px; color: var(--ink);
  }
  .form-col { position: absolute; top: 360px; width: 370px; }
  .form-col--main { left: 172px; }
  .form-col--guest { left: 644px; }
  .form-col__title { font-family: "Dosis", sans-serif; font-weight: 600; font-size: 22px; line-height: 22px; color: var(--ink); margin-bottom: 26px; }
  .field {
    display: block; width: 369px; height: 40px; margin-bottom: 15px; padding: 0 18px;
    border: 1px dotted var(--field-border); background: rgba(255,255,255,0.15);
    font-family: "Dosis", sans-serif; font-size: 14px; color: var(--ink);
  }
  .field::placeholder { color: var(--ink); }
  .btn {
    position: absolute; top: 587px; width: 178px; height: 38px; border: 0; border-radius: 2px;
    background: var(--brand-red); color: var(--white);
    font-family: "Bree Serif", serif; font-size: 15px; cursor: pointer;
  }
  .btn--more { left: 360px; }
  .btn--submit { left: 837px; }
  .event-band {
    position: absolute; left: 0; top: 756px; width: 1200px; height: 153px; background: var(--pine);
  }
  .event-band::before {
    content: ""; position: absolute; left: 0; top: -9px; width: 1200px; height: 10px;
    background: radial-gradient(ellipse 17px 10px at 50% 100%, var(--pine) 97%, rgba(31,94,53,0) 100%) repeat-x;
    background-size: 33px 10px;
  }
  .event-info {
    position: absolute; top: 790px; left: 0; width: 1200px; height: 100px;
    font-family: "Lobster", cursive; font-size: 26px; color: var(--white); line-height: 44px; text-align: center;
  }
  .event-info__col { position: absolute; top: 0; width: 360px; }
  .event-info__col--contact { left: 135px; }
  .event-info__col--place { left: 457px; }
  .event-info__col--date { left: 743px; }
  .partners {
    position: absolute; top: 909px; left: 0; width: 1200px; height: 65px; background: var(--white);
    display: flex; align-items: center; justify-content: space-between; padding: 0 50px;
    font-family: "Dosis", sans-serif; font-weight: 600; font-size: 20px; color: var(--partner-ink);
  }
</style>
</head>
<body>
  <div class="corner-decor corner-decor--left" role="img" aria-label="Tannenzweige mit goldenen Glocken und roten Weihnachtskugeln"></div>
  <div class="corner-decor corner-decor--right" role="img" aria-label="Tannenzweige mit goldenen Glocken und roten Weihnachtskugeln"></div>

  <header class="brand">
    <div class="brand__name">Lumenar</div>
    <span class="brand__tag">IT SOLUTIONS</span>
  </header>

  <p class="intro">Ob Sie den ganzen Abend bleiben oder nur kurz nach dem Weihnachts-Shopping vorbeischauen, ist ganz Ihnen überlassen. Wir freuen uns sehr, wenn Sie uns die Gelegenheit geben, Ihnen mit dieser Einladung für die erfolgreiche Zusammenarbeit herzlichst zu danken.</p>

  <form>
    <section class="form-col form-col--main">
      <h2 class="form-col__title">Ihre Anmeldung</h2>
      <input class="field" type="email" placeholder="Ihre E-Mail-Adresse">
      <input class="field" type="text" placeholder="Vorname">
      <input class="field" type="text" placeholder="Nachname">
    </section>
    <section class="form-col form-col--guest">
      <h2 class="form-col__title">Ihre Begleitperson</h2>
      <input class="field" type="text" placeholder="Vorname">
      <input class="field" type="text" placeholder="Nachname">
      <input class="field" type="text" placeholder="Firma (Optional)">
    </section>
    <button class="btn btn--more" type="button">Weitere Begleitperson</button>
    <button class="btn btn--submit" type="submit">Absenden</button>
  </form>

  <div class="event-band" aria-hidden="true"></div>

  <footer class="event-info">
    <div class="event-info__col event-info__col--contact">Telefon - 041 555 01 23<br>E-Mail - info@lumenar-it.ch</div>
    <div class="event-info__col event-info__col--place">Lindenweg 12<br>6000 Seestadt</div>
    <div class="event-info__col event-info__col--date">17. Dezember 2016<br>17 - 20 Uhr</div>
  </footer>

  <div class="partners">
    <span>Corvo</span><span>Brightline</span><span>Nexari</span><span>Tallis</span><span>Quorin</span><span>Veltra</span><span>Ardent</span><span>Solvane</span><span>Kestro</span><span>Pylon</span><span>Marvex</span>
  </div>
</body>
</html>
```